Morlavik APP redesign and color change

I am looking for a new design for my app. Please see the attached current design.

Currently, I have a functioning app but the colors and design are awful!
The logo is great but the rest of the app needs a refresh.
(Logo hi res not yet available but will upload soon.)
New colors or anything that is cutting edge.

Basically: It is a secure social media app within a school system where the teachers, students and parents can text, exchange photos, plan curriculum, etc.

I NEED ONLY landing page with a new look!
Looking for one distinct design for the landing page with new look.
The developer will apply this one design towards the rest of the pages/app screens.

Because part of the social media I need the feel and look of what is now the trend. Something that will attract and keep the client(s) interested. I am really leaving all the creative work to the designer and open to any suggestions.

Target Market(s)

Schools, community, teachers, students, colleges, sport teams

Industry/Entity Type

Non Profit

Font styles to use
Serif
Sans Serif

Colors

Designer to choose colors to be used in the design.

Requirements
Must have
• Sharp, trendy, millennial feel
Nice to have
• Up to designer
Should not have
• Up to designer

```html
<!DOCTYPE html>
<html lang="en">
<head>
<meta charset="utf-8">
<title>Morlavik — Sign In</title>
<link rel="stylesheet" href="https://fonts.googleapis.com/css2?family=Lato:wght@400;700;900&display=swap">
<style>
  :root {
    --olive-deep: #3b4800;
    --olive: #5b6e00;
    --brand-ink: #4a5400;
    --amber: #b87800;
    --amber-label: #b07a00;
    --ink: #2b2b2b;
    --rule: #6a6a6a;
    --white: #ffffff;
    --panel: rgba(255, 255, 255, 0.74);
    --photo-top: #6b5a48;
    --photo-mid: #8fa36a;
    --photo-low: #5f8a2e;
  }
  * { box-sizing: border-box; margin: 0; padding: 0; }
  html, body { width: 741px; height: 1200px; overflow: hidden; }
  body { font-family: "Lato", sans-serif; background: var(--olive-deep); }

  .screen { position: relative; width: 741px; height: 1200px; overflow: hidden; }

  .hero-photo {
    position: absolute; left: 0; top: 0; width: 741px; height: 1023px;
    background:
      radial-gradient(ellipse at 55% 45%, #efe4c4 0%, rgba(239,228,196,0.55) 22%, rgba(239,228,196,0) 45%),
      linear-gradient(180deg, var(--photo-top) 0%, #7d7358 18%, var(--photo-mid) 40%, #7ea04a 62%, var(--photo-low) 100%);
  }

  .footer-band {
    position: absolute; left: 0; top: 1023px; width: 741px; height: 177px;
    background: linear-gradient(180deg, var(--olive-deep) 0%, var(--olive) 100%);
  }

  .brand-name {
    position: absolute; left: 0; top: 540px; width: 741px; text-align: center;
    font-weight: 900; font-size: 35px; letter-spacing: 14px; color: var(--brand-ink);
    padding-left: 14px;
  }

  .login-card { position: absolute; left: 93px; top: 653px; width: 555px; }
  .login-fields { background: var(--panel); height: 317px; padding: 60px 61px 0 61px; }

  .field-label {
    display: block; font-size: 16px; font-weight: 700; letter-spacing: 1.6px;
    color: var(--amber-label); text-transform: uppercase;
  }
  .field-value { font-size: 23px; color: var(--ink); margin-top: 13px; }
  .field-username { border-bottom: 2px solid var(--rule); height: 105px; }
  .field-password { margin-top: 39px; }
  .password-dots { display: flex; gap: 9px; margin-top: 25px; }
  .password-dots span { width: 9px; height: 9px; border-radius: 50%; background: var(--ink); }

  .start-button {
    display: flex; align-items: center; justify-content: space-between;
    height: 106px; padding: 0 60px 0 61px; background: var(--amber);
    color: var(--white); font-size: 23px;
  }

  .signup-link {
    position: absolute; left: 0; top: 1119px; width: 741px; text-align: center;
    color: var(--white); font-size: 18px;
  }
</style>
</head>
<body>
<main class="screen">
  <div class="hero-photo" role="img" aria-label="Photo of a girl in a sun hat reading a book on the grass beneath a tree in a garden"></div>
  <div class="footer-band"></div>

  <div class="brand-name">MORLAVIK</div>

  <form class="login-card">
    <div class="login-fields">
      <div class="field-username">
        <span class="field-label">Username</span>
        <div class="field-value">ellis@mailbox.net</div>
      </div>
      <div class="field-password">
        <span class="field-label">Password</span>
        <div class="password-dots"><span></span><span></span><span></span><span></span><span></span><span></span><span></span><span></span></div>
      </div>
    </div>
    <div class="start-button">
      <span>Get Started</span>
      <svg width="14" height="18" viewBox="0 0 14 18" aria-hidden="true"><polygon points="0,0 14,9 0,18" fill="#111"/></svg>
    </div>
  </form>

  <p class="signup-link">Not registered? Create Account</p>
</main>
</body>
</html>
```